Business card for a new cabinet shop company named Veloran Cabinets for high end cabinets

Design a business card, thinking dark rich green with colours to speak of high end luxury ie; cream, gold, black possibly

Mitchell Tarrowby
Director Craftsman
Email: info@veloranjoinery-example.com.au
Instagram : @veloran.cabinets

```html
<!DOCTYPE html>
<html lang="en">
<head>
<meta charset="utf-8">
<title>Veloran Cabinets – Business Card</title>
<link href="https://fonts.googleapis.com/css2?family=Jost:wght@400;500&family=Montserrat:wght@700&display=swap" rel="stylesheet">
<style>
  :root {
    --backdrop: #1a1b1a;
    --green: #07402a;
    --green-deep: #063a26;
    --green-pattern: #0b4a31;
    --gold: #c9a962;
    --cream: #f6f2e8;
  }
  * { box-sizing: border-box; margin: 0; padding: 0; }
  html, body {
    width: 1200px; height: 801px; overflow: hidden;
    background: var(--backdrop);
  }
  .canvas {
    position: relative; width: 1200px; height: 801px;
    display: flex; align-items: center; justify-content: center; gap: 44px;
  }
  .card {
    position: relative; width: 530px; height: 303px;
    background: var(--green); overflow: hidden;
    box-shadow: 0 18px 40px rgba(0,0,0,.5);
  }
  /* Contact side */
  .card--contact { border-bottom: 5px solid var(--gold); }
  .brand {
    position: absolute; left: 0; top: 0; width: 262px; height: 100%;
    display: flex; align-items: center; justify-content: center; gap: 12px;
  }
  .brand__mark {
    width: 14px; height: 14px; border: 2px solid var(--gold);
  }
  .brand__name {
    font-family: "Jost", sans-serif; font-weight: 500;
    font-size: 27px; color: var(--gold); letter-spacing: .5px;
  }
  .divider {
    position: absolute; left: 262px; top: 88px; width: 1.5px; height: 124px;
    background: var(--gold);
  }
  .details {
    position: absolute; left: 288px; top: 84px; right: 14px;
  }
  .details__name {
    font-family: "Montserrat", sans-serif; font-weight: 700;
    font-size: 22px; color: var(--gold); line-height: 1.1; white-space: nowrap;
  }
  .details__role {
    font-family: "Jost", sans-serif; font-size: 13px; color: var(--cream);
    margin: 4px 0 16px;
  }
  .contact-list { list-style: none; }
  .contact-list li {
    display: flex; align-items: center; gap: 8px;
    font-family: "Jost", sans-serif; font-size: 11.5px; color: var(--cream);
    margin-bottom: 7px; white-space: nowrap;
  }
  .contact-list svg { width: 13px; height: 13px; flex: none; }
  /* Brand side */
  .card--brand { background: var(--green-deep); }
  .pattern-field {
    position: absolute; inset: 0;
    background: linear-gradient(135deg, var(--green-pattern), var(--green-deep));
  }
  .card--brand .brand {
    width: 100%; gap: 16px;
  }
  .card--brand .brand__mark { width: 22px; height: 22px; border-width: 3px; }
  .card--brand .brand__name { font-size: 44px; }
</style>
</head>
<body>
<main class="canvas">
  <section class="card card--contact" aria-label="Business card, contact side">
    <div class="brand">
      <span class="brand__mark" aria-hidden="true"></span>
      <span class="brand__name">Veloran Cabinets</span>
    </div>
    <div class="divider" aria-hidden="true"></div>
    <div class="details">
      <p class="details__name">Mitchell Tarrowby</p>
      <p class="details__role">Director Craftsman</p>
      <ul class="contact-list">
        <li>
          <svg viewBox="0 0 14 14" aria-hidden="true"><circle cx="7" cy="7" r="6" fill="var(--gold)"/></svg>
          @veloran.cabinets
        </li>
        <li>
          <svg viewBox="0 0 14 14" aria-hidden="true"><rect x="1" y="3" width="12" height="8" fill="var(--gold)"/><path d="M1 3l6 5 6-5" fill="none" stroke="var(--green)" stroke-width="1.2"/></svg>
          info@veloranjoinery-example.com.au
        </li>
        <li>
          <svg viewBox="0 0 14 14" aria-hidden="true"><circle cx="7" cy="7" r="6" fill="none" stroke="var(--gold)" stroke-width="1.4"/><ellipse cx="7" cy="7" rx="2.6" ry="6" fill="none" stroke="var(--gold)" stroke-width="1.1"/><path d="M1 7h12" stroke="var(--gold)" stroke-width="1.1"/></svg>
          veloranjoinery-example.com.au
        </li>
      </ul>
    </div>
  </section>

  <section class="card card--brand" aria-label="Business card, brand side">
    <div class="pattern-field" role="img" aria-label="Faint tonal repeat pattern of the brand symbol across the card"></div>
    <div class="brand">
      <span class="brand__mark" aria-hidden="true"></span>
      <span class="brand__name">Veloran Cabinets</span>
    </div>
  </section>
</main>
</body>
</html>
```